Aid, Development & Consulting Firm

Brantwell Fennimore Consulting Pty Ltd is a small firm in Australia whose principal works in the area of aid and development. His experience is broad ranging from aid project design and evaluation; to offering security advice in running aid operations in dangerous situations. He works with governments and private firms in conducting training for personnel travelling to work in dangerous or difficult regions. He has worked for many years with NGO's (aid organisations) and consults to the WCA. He works in locations all over the globe which include trouble spots like Iraq and Sudan, to sleepier locales like Samoa and Fiji. Being on Asia's doorstep much time is spent in Asia eg Indonesia, Vietnam. He is often called on to monitor and evaluate aid projects throughtout the globe.

Target Market(s)

Government Aid Divisions eg in Oz, PacRelief; WCA; NGO's and consulting firms who work in developing countries

Industry/Entity Type

Security

Requirements
Nice to have
• Try and incorporate a global feel without being obvious i.e. no starving children as the primary work done is a step beyond obvious aid relief. Something very simple but bold and stylish as card holder is not a "touchy" feely person
Should not have
• No starving kid type scenarios. Prefer no pictures

```html
<!DOCTYPE html>
<html lang="en">
<head>
<meta charset="utf-8">
<title>Brantwell Fennimore Consulting – Business Card</title>
<link rel="stylesheet" href="https://fonts.googleapis.com/css2?family=Archivo:wght@700&family=Open+Sans:wght@400;600&display=swap">
<style>
  :root {
    --page-bg: #e9e6e1;
    --card-black: #0c0c0d;
    --card-black-soft: #1b1c1e;
    --card-white: #ffffff;
    --brand-blue: #2aa7d6;
    --brand-blue-light: #3cc4ef;
    --name-grey: #4a4a4a;
    --text-white: #f2f2f2;
    --text-muted: #c9c9c9;
  }
  * { box-sizing: border-box; margin: 0; padding: 0; }
  html, body {
    width: 1200px;
    height: 900px;
    overflow: hidden;
    background: var(--page-bg);
  }
  .canvas {
    position: relative;
    width: 1200px;
    height: 900px;
  }
  .card {
    position: absolute;
    width: 540px;
    height: 310px;
    overflow: hidden;
    box-shadow: 0 8px 22px rgba(0,0,0,0.25);
  }

  /* Brand placeholder: plain square + name in one colour and weight */
  .brand-lockup {
    position: absolute;
    left: 0; right: 0;
    display: flex;
    justify-content: center;
    align-items: center;
    gap: 12px;
  }
  .brand-square {
    width: 30px;
    height: 30px;
    background: var(--brand-blue);
    flex: none;
  }
  .brand-name {
    font-family: "Archivo", sans-serif;
    font-weight: 700;
    font-size: 34px;
    line-height: 1;
    color: var(--brand-blue);
  }
  .company-name {
    position: absolute;
    left: 0; right: 0;
    text-align: center;
    font-family: "Archivo", sans-serif;
    font-weight: 700;
    font-size: 17px;
    letter-spacing: 0.2px;
    text-transform: uppercase;
  }

  /* Front card */
  .card--front {
    left: 50px;
    top: 160px;
    background: linear-gradient(160deg, var(--card-black-soft) 0%, var(--card-black) 70%);
  }
  .card--front .brand-lockup { top: 102px; }
  .card--front .company-name {
    top: 168px;
    color: var(--text-white);
  }
  .front-email {
    position: absolute;
    right: 56px;
    bottom: 44px;
    font-family: "Open Sans", sans-serif;
    font-size: 14px;
    color: var(--brand-blue);
  }

  /* Back card */
  .card--back {
    left: 610px;
    top: 430px;
    background: var(--card-white);
  }
  .card--back .brand-lockup { top: 54px; }
  .card--back .brand-square { width: 26px; height: 26px; }
  .card--back .brand-name { font-size: 30px; }
  .card--back .company-name {
    top: 112px;
    color: var(--name-grey);
    font-size: 15px;
  }
  .info-band {
    position: absolute;
    left: 0; top: 0;
    width: 540px;
    height: 310px;
  }
  .address-block {
    position: absolute;
    left: 26px;
    top: 206px;
    font-family: "Open Sans", sans-serif;
    font-size: 12.5px;
    line-height: 17px;
    color: var(--text-white);
  }
  .contact-line {
    display: flex;
    align-items: center;
    gap: 6px;
  }
  .contact-line svg { flex: none; }
  .person-block {
    position: absolute;
    left: 350px;
    top: 192px;
    font-family: "Open Sans", sans-serif;
    color: var(--text-white);
  }
  .person-name {
    font-weight: 600;
    font-size: 14px;
    color: var(--brand-blue-light);
  }
  .person-role {
    font-size: 12px;
    color: var(--text-muted);
    margin-bottom: 12px;
  }
  .person-email { font-size: 12.5px; }
</style>
</head>
<body>
<main class="canvas">

  <section class="card card--front" aria-label="Business card front">
    <div class="brand-lockup">
      <span class="brand-square" aria-hidden="true"></span>
      <span class="brand-name">Brantwell Fennimore</span>
    </div>
    <div class="company-name">Brantwell Fennimore Consulting Pty Ltd</div>
    <div class="front-email">brantwellf@mailbox.com</div>
  </section>

  <section class="card card--back" aria-label="Business card back">
    <div class="brand-lockup">
      <span class="brand-square" aria-hidden="true"></span>
      <span class="brand-name">Brantwell Fennimore</span>
    </div>
    <div class="company-name">Brantwell Fennimore Consulting Pty Ltd</div>

    <svg class="info-band" viewBox="0 0 540 310" aria-hidden="true">
      <defs>
        <linearGradient id="stripGradient" x1="0" x2="1" y1="0" y2="0">
          <stop offset="0" stop-color="#1584b0"/>
          <stop offset="0.55" stop-color="#3cc4ef"/>
          <stop offset="1" stop-color="#1584b0"/>
        </linearGradient>
      </defs>
      <path d="M0 178 H318 L326 168 L334 178 V162 H540 V310 H0 Z" fill="#0c0c0d"/>
      <rect x="0" y="298" width="540" height="12" fill="url(#stripGradient)"/>
    </svg>

    <div class="address-block">
      <div>14 Harlow Street, Kent Town,</div>
      <div>SA, 5067 Australia</div>
      <div class="contact-line">
        <svg width="10" height="10" viewBox="0 0 10 10" aria-hidden="true"><path d="M2 0.8 L3.6 2.8 L2.8 3.8 Q4 6 6.2 7.2 L7.2 6.4 L9.2 8 L8 9.4 Q3.5 9 0.6 2 Z" fill="#3cc4ef"/></svg>
        <span>+61 8 8000 1234</span>
      </div>
      <div class="contact-line">
        <svg width="10" height="12" viewBox="0 0 10 12" aria-hidden="true"><rect x="1.5" y="0.8" width="7" height="10.4" rx="1" fill="none" stroke="#3cc4ef" stroke-width="1.3"/></svg>
        <span>+61 (0) 400 555 018</span>
      </div>
    </div>

    <div class="person-block">
      <div class="person-name">B. Brantwell Fennimore</div>
      <div class="person-role">Director</div>
      <div class="contact-line person-email">
        <svg width="11" height="8" viewBox="0 0 11 8" aria-hidden="true"><rect x="0" y="0" width="11" height="8" fill="#3cc4ef"/><path d="M0 0 L5.5 4.5 L11 0" fill="none" stroke="#0c0c0d" stroke-width="1"/></svg>
        <span>brantwell@netlink.com.au</span>
      </div>
    </div>
  </section>

</main>
</body>
</html>
```